One of a kind, 100% Pure & Natural Skincare line needs stunning product label

We need product label design for new natural skincare company called Tolven & Mira Skincare. We create luxurious, 100% pure & natural skincare that is free from ingredients that may be potentially irritating to the skin. No toxins, preservatives or additives. Our initial product is Harbor Face Balm, a nourishing face cream that suits discerning women with mature skin and those with dry/sensitive skin needing extra hydration. Also those that choose to minimize their exposure to environmental toxins. Our brand is simple yet elegant, supporting a holistic, authentic lifestyle and embracing natural skincare.

Target Market(s)

Discerning women with mature skin and those with dry/sensitive skin needing extra hydration. Also those that choose to minimize their exposure to environmental toxins.

Industry/Entity Type

Skin Care Product

Font styles to use
Sans Serif
Script

Colors
f9d9e8
fef1ee

Requirements
Must have
• The Logo.
HARBOR FACE BALM
EMBRACING NATURAL SKINCARE
Labels must be feminine, simple/minimal yet stylish. Uncluttered yet elegant.
This is a very natural product with minimal ingredients.
Nice to have
• The logo can be incorporated in to the label, or It can be left separate as a sticker on top of the jar. The product is a firm balm consistency and is in frosted glass jars with matt silver lids.
Jar height is 45mm, width is 60mm.
Label height: 28mm and length 185mm
Should not have
• Natural or farmers market type theme. No Bold/loud lettering.

```html
<!DOCTYPE html>
<html lang="en">
<head>
<meta charset="utf-8">
<title>Harbor Face Balm – Jar Label</title>
<link rel="stylesheet" href="https://fonts.googleapis.com/css2?family=Montserrat:wght@400;500;600&display=swap">
<style>
  :root {
    --page-bg: #ffffff;
    --ink: #1c1c1c;
    --ink-soft: #3a3a3a;
    --bleed-line: #b9d6ea;
    --trim-line: #6d6d6d;
    --blush-deep: #f4bfcd;
    --blush: #f9d9e8;
    --blush-light: #fef1ee;
    --white: #ffffff;
  }
  * { box-sizing: border-box; margin: 0; padding: 0; }
  html, body {
    width: 1200px; height: 1000px; overflow: hidden;
    background: var(--page-bg);
    font-family: "Montserrat", sans-serif;
    color: var(--ink);
  }
  .canvas { position: relative; width: 1200px; height: 1000px; }

  .bleed {
    position: absolute; left: 40px; top: 398px;
    width: 1134px; height: 204px;
    border: 1px dashed var(--bleed-line);
  }
  .label {
    position: absolute; left: 18px; top: 18px;
    width: 1096px; height: 167px;
    border: 1px solid var(--trim-line);
    background: var(--white);
    overflow: hidden;
  }
  .front-panel {
    position: absolute; left: 348px; top: 0; bottom: 0; width: 400px;
    background: linear-gradient(90deg, var(--blush-deep) 0%, var(--blush) 40%, var(--blush-light) 75%, var(--white) 100%);
    text-align: center;
  }
  .product-name {
    position: absolute; left: 0; right: 0; top: 55px;
    font-size: 29px; font-weight: 400; letter-spacing: 0.3px;
  }
  .name-rule {
    position: absolute; left: 80px; width: 225px; top: 88px;
    height: 1px; background: var(--ink);
  }
  .tagline {
    position: absolute; left: 0; right: 0; top: 95px;
    font-size: 12px; letter-spacing: 0.4px; color: var(--ink-soft);
  }
  .volume {
    position: absolute; left: 0; right: 0; top: 130px;
    font-size: 6.5px; font-weight: 500;
  }

  .safe-area {
    position: absolute; top: 18px; height: 128px;
    border: 1px dashed var(--bleed-line);
    font-size: 9.6px; line-height: 1.35; color: var(--ink);
  }
  .info-left { left: 18px; width: 330px; padding: 7px 6px; }
  .info-right { left: 746px; width: 330px; padding: 2px 6px; }
  .safe-area p { margin-bottom: 9px; }
  .safe-area strong { font-weight: 600; }
  .info-left .allergy { margin-top: 18px; }
  .info-right p { margin-bottom: 8px; }

  .pao-icon { position: absolute; right: 6px; bottom: 4px; width: 26px; height: 24px; }
</style>
</head>
<body>
<div class="canvas">
  <div class="bleed">
    <div class="label">
      <section class="safe-area info-left">
        <p><strong>INGREDIENTS :</strong>&nbsp; Tallow from pasture raised goats, frankincense, sandalwood &amp; myrrh essential oils.</p>
        <p><strong>DIRECTIONS :</strong>&nbsp; Soften small amount in palm of<br>hand &amp; gently massage into skin as often as</p>
        <p class="allergy">Allergy patch test recommended. If irritation occurs, discon-<br>tinue use.</p>
      </section>

      <section class="front-panel">
        <h1 class="product-name">HARBOR FACE BALM</h1>
        <div class="name-rule"></div>
        <p class="tagline">EMBRACING NATURAL SKINCARE</p>
        <p class="volume">50 ml</p>
      </section>

      <section class="safe-area info-right">
        <p><strong>CAUTION:</strong>&nbsp; Keep out of reach of children. If pregnant or breastfeeding, consult your healthcare practitioner. Avoid contact with eyes &amp; sensitive areas.</p>
        <p>Store below 25°C</p>
        <p>MADE IN AUSTRALIA</p>
        <p>B#</p>
        <p>info@tolvenandmiraskincare.com.au</p>
        <svg class="pao-icon" viewBox="0 0 26 24" aria-label="Use within 6 months of opening">
          <path d="M4 10 L22 10 L20 22 L6 22 Z" fill="none" stroke="#1c1c1c" stroke-width="1.4"/>
          <path d="M4 8 L10 2 L22 6" fill="none" stroke="#1c1c1c" stroke-width="1.4"/>
          <rect x="7" y="13" width="12" height="6" fill="#1c1c1c"/>
          <text x="13" y="18.2" font-family="Montserrat, sans-serif" font-size="5" fill="#fff" text-anchor="middle" font-weight="600">6M</text>
        </svg>
      </section>
    </div>
  </div>
</div>
</body>
</html>
```